Personal Injury Lawyer Billboard

I would like a design created featuring the image of the lawyer centered in the middle of the design.
To the left of the lawyer's image it should read "INJURED?"
To the right of the lawyer's image, it should read "CALL DEAN!"
Under Call Dean, include the phone number 318-555-0187.
At the bottom of the design include the lawyers information "Dean Marlowe Accident & Injury Lawyers"
PLEASE REMOVED THE BACKGROUND IMAGERY OF THE PHOTO SUBMITTED. Also, the colors for this design should match the colors shown in the logo (navy, white and relective soft gold). Please use those color combinations in ways that best stand out.

```html
<!DOCTYPE html>
<html lang="en">
<head>
<meta charset="utf-8">
<title>Dean Marlowe Accident &amp; Injury Lawyers – Billboard</title>
<link rel="stylesheet" href="https://fonts.googleapis.com/css2?family=Bebas+Neue&family=Poppins:wght@400&display=swap">
<style>
  :root {
    --backdrop: #a4a4a4;
    --white: #ffffff;
    --navy: #0b1a45;
    --gold: #e3bd4a;
    --red: #c00000;
    --ink: #0a0a0a;
    --photo-top: #d9dce4;
    --photo-bottom: #1f2f63;
  }
  html, body {
    margin: 0;
    padding: 0;
    width: 1200px;
    height: 600px;
    overflow: hidden;
    background: var(--backdrop);
  }
  .billboard {
    position: absolute;
    left: 37px;
    top: 136px;
    width: 1125px;
    height: 328px;
  }
  .headline { font-family: "Bebas Neue", "Oswald", sans-serif; }
  .headline--question { fill: var(--red); }
  .headline--call { fill: var(--navy); }
  .phone-number { font-family: "Bebas Neue", "Oswald", sans-serif; fill: var(--ink); }
  .firm-name { font-family: "Bebas Neue", "Oswald", sans-serif; fill: var(--white); }
  .firm-caption { font-family: "Poppins", sans-serif; fill: var(--white); font-size: 21px; }
</style>
</head>
<body>
<svg class="billboard" viewBox="0 0 1125 328" width="1125" height="328" xmlns="http://www.w3.org/2000/svg">
  <defs>
    <clipPath id="board-clip"><rect width="1125" height="328"/></clipPath>
    <linearGradient id="portrait-fill" x1="0" y1="0" x2="0" y2="1">
      <stop offset="0" stop-color="var(--photo-top)"/>
      <stop offset="0.45" stop-color="var(--photo-bottom)"/>
      <stop offset="1" stop-color="var(--navy)"/>
    </linearGradient>
  </defs>
  <g clip-path="url(#board-clip)">
    <!-- base -->
    <rect class="board-base" width="1125" height="328" fill="var(--white)"/>
    <!-- left navy band -->
    <rect class="band-navy-left" x="0" y="164" width="560" height="164" fill="var(--navy)"/>
    <!-- right gold band -->
    <rect class="band-gold" x="671" y="164" width="454" height="73" fill="var(--gold)"/>
    <!-- right navy band -->
    <rect class="band-navy-right" x="728" y="237" width="397" height="91" fill="var(--navy)"/>
    <!-- portrait disc -->
    <circle class="portrait-ring" cx="569" cy="299" r="168" fill="var(--white)" stroke="var(--gold)" stroke-width="5"/>
    <!-- portrait area -->
    <path class="portrait" role="img" aria-label="Cut-out portrait of the lawyer in a navy suit and green tie, raising a fist"
          d="M430 328 L436 245 Q446 222 495 208 L505 190 Q492 150 500 110 Q505 30 565 24 Q625 30 630 110 Q634 150 622 180 L630 205 Q680 220 690 255 L700 328 Z"
          fill="url(#portrait-fill)"/>
  </g>

  <!-- headlines -->
  <text class="headline headline--question" x="50" y="146" font-size="150" textLength="411" lengthAdjust="spacingAndGlyphs">INJURED?</text>
  <text class="headline headline--call" x="659" y="137" font-size="126" textLength="417" lengthAdjust="spacingAndGlyphs">CALL DEAN!</text>

  <!-- phone -->
  <text class="phone-number" x="755" y="227" font-size="73" textLength="321" lengthAdjust="spacingAndGlyphs">318-555-0187</text>

  <!-- firm name (left) -->
  <text class="firm-name" x="53" y="240" font-size="62" textLength="313" lengthAdjust="spacingAndGlyphs">DEAN MARLOWE</text>
  <text class="firm-name" x="53" y="284" font-size="34" textLength="315" lengthAdjust="spacingAndGlyphs">ACCIDENT &amp; INJURY LAWYERS</text>

  <!-- firm caption (right) -->
  <text class="firm-caption" x="1073" y="272" text-anchor="end">Dean Marlowe Accident</text>
  <text class="firm-caption" x="1073" y="300" text-anchor="end">&amp; Injury Lawyers</text>
</svg>
</body>
</html>
```